"Cedar Hollow Realty" is the name of my real estate company

This is for a: "for sale" sign, looking for a minimalist design, wire frame outline of a midcentury modern homes roof line or elevation?

My name is: Dean Marlowe (needed)
My Cell # is: 415 208 3947 (needed)
My BRE license # is: 02468135 (needed)
BRE needs to be displayed in this format: BRE 02468135 (needed)
The white outline on the sign riders 'pictured" may work on large sign
Note font on pictured rider sign

This design is for a real estate "for sale" sign or sandwich board sign. Do Not include the words "For Sale" on the sign.

The measurements are 36" inches (91.44 cm) Length, or tall X 24" inches (60.90 cm) Wide.

|
3
---- 24 ----
6
|

Sorry I wasn't more specific earlier. I'd like the elements of the sign to be scaled in size according to their importance, from largest to smallest:

My name: Dean Marlowe
My phone number: 415-208-3947
My company name: Cedar Hollow Realty
My license number: BRE 02468135 (This can be much smaller than the smallest text)
Additionally, please incorporate contemporary to mid-century modern elements on the wire frame roofline or a simple roof-like design.

Thank you!

Best regards,
Dean

```html
<!DOCTYPE html>
<html lang="en">
<head>
<meta charset="utf-8">
<title>Dean Marlowe – Cedar Hollow Realty Sign</title>
<link rel="stylesheet" href="https://fonts.googleapis.com/css2?family=Josefin+Sans:wght@400;600;700&display=swap">
<style>
  :root {
    --sign-black: #141414;
    --sign-white: #ffffff;
  }
  html, body {
    margin: 0;
    padding: 0;
    width: 802px;
    height: 1200px;
    overflow: hidden;
    background: var(--sign-black);
  }
  .sign {
    position: relative;
    width: 802px;
    height: 1200px;
    background: var(--sign-black);
    color: var(--sign-white);
    font-family: "Josefin Sans", "Century Gothic", sans-serif;
    overflow: hidden;
  }
  .sign__frame {
    position: absolute;
    left: 16px;
    top: 16px;
    right: 16px;
    bottom: 16px;
    border: 5px solid var(--sign-white);
  }
  .agent-name {
    position: absolute;
    left: 75px;
    top: 232px;
    margin: 0;
    font-size: 70px;
    font-weight: 600;
    line-height: 1;
    letter-spacing: 2px;
    text-transform: uppercase;
    white-space: nowrap;
  }
  .license {
    position: absolute;
    left: 77px;
    top: 326px;
    margin: 0;
    font-size: 24px;
    font-weight: 400;
    line-height: 1;
    letter-spacing: 2px;
  }
  .roofline {
    position: absolute;
    left: 75px;
    top: 400px;
    width: 652px;
    height: 160px;
  }
  .roofline path,
  .roofline line {
    fill: none;
    stroke: var(--sign-white);
    stroke-width: 4;
    stroke-linecap: square;
    stroke-linejoin: miter;
  }
  .company-name {
    position: absolute;
    left: 75px;
    top: 592px;
    margin: 0;
    font-size: 40px;
    font-weight: 600;
    line-height: 1;
    letter-spacing: 3px;
    text-transform: uppercase;
    white-space: nowrap;
  }
  .call-label {
    position: absolute;
    left: 75px;
    top: 700px;
    margin: 0;
    font-size: 40px;
    font-weight: 600;
    line-height: 1;
    letter-spacing: 2px;
    text-transform: uppercase;
  }
  .phone-band {
    position: absolute;
    left: 16px;
    right: 16px;
    top: 767px;
    height: 147px;
    background: var(--sign-white);
    color: var(--sign-black);
    display: flex;
    align-items: center;
  }
  .phone-number {
    margin: 8px 0 0 59px;
    font-size: 64px;
    font-weight: 600;
    line-height: 1;
    letter-spacing: 4px;
    white-space: nowrap;
  }
</style>
</head>
<body>
  <main class="sign">
    <div class="sign__frame"></div>
    <h1 class="agent-name">Dean Marlowe</h1>
    <p class="license">BRE 02468135</p>
    <svg class="roofline" viewBox="0 0 652 160" aria-hidden="true">
      <path d="M0 30 L330 80 L652 10"/>
      <line x1="40" y1="36" x2="40" y2="156"/>
      <line x1="612" y1="20" x2="612" y2="156"/>
      <line x1="330" y1="80" x2="330" y2="156"/>
      <path d="M380 90 L560 90 L560 156"/>
      <line x1="90" y1="100" x2="280" y2="100"/>
      <line x1="0" y1="156" x2="652" y2="156"/>
    </svg>
    <p class="company-name">Cedar Hollow Realty</p>
    <p class="call-label">Call me:</p>
    <div class="phone-band">
      <p class="phone-number">415.208.3947</p>
    </div>
  </main>
</body>
</html>
```